Yacht, Boats, Watersports company needs a redesign of business card

Hello Designers!
We are a Boat dealership company that sells fun in the water, we sell boats, Yachts, Kayaks and also yacht WaterSport toys. We are looking to redesign our business cards in to something a little bit more sophisticated. in a way that we can make better use of our company colors. I'm attaching a zipped file containing the company 3 sets of company logo which one is an horizontal another one is a vertical and also a chromed 3d logo. Also is included two set of business cards that we use and also some designs that i think it's interesting. We use PMS 2026c Orange and PMS 7687C Blue. I would like to see at least two different options with the orange as accent and also using blue as an accent color. It's really important for the business cards to have a font option and size that is legible to most people. Our current website is wwww.coralpennant.com. Please visit if you want to have a better feeling of the Boat dealership
You can send Single sided or double side options. We are now using single sided but we may be open for a double side option if we really like the design.
Target Market(s)
Marine, boat sales, yacht sales, water toys sales/
Contact Information for Business Card
Name: Dale Whitcombe
Address: 212 North Fenwick Lane,
Palm Cove, FL 33019
Phone: 954-731-8842
Fax: 954:731-8843
Cell: 954-382-1490
Email: dw@coralpennant.com
Website: coralpennant.com
Requirements
Must have
- the current information of the business card provided.
logo
use the PMS Colors
Nice to have
- a touch of elegance and sophistication but simple
Should not have
- should not have any typography that is hard to read, the card should be simple but yet sophisticated.

```html
<!DOCTYPE html>
<html lang="en">
<head>
<meta charset="utf-8">
<title>Coral Pennant — Business Card</title>
<link href="https://fonts.googleapis.com/css2?family=Arimo:wght@400;700&family=Bebas+Neue&display=swap" rel="stylesheet">
<style>
  :root {
    --page: #0e0e0e;
    --card: #1b1b1b;
    --orange: #f0652d;
    --ink: #f2f2f2;
    --rule: #6a6a6a;
  }
  * { box-sizing: border-box; margin: 0; padding: 0; }
  html, body { width: 1200px; height: 900px; overflow: hidden; }
  body {
    background: var(--page);
    font-family: "Arimo", Arial, sans-serif;
    position: relative;
  }
  .card {
    position: absolute;
    left: 320px;
    width: 560px;
    height: 320px;
    background: var(--card);
    box-shadow: 0 10px 30px rgba(0,0,0,.6);
  }
  .card--front { top: 100px; }
  .card--back { top: 470px; }

  .brand {
    position: absolute;
    left: 90px;
    top: 128px;
    display: flex;
    align-items: center;
    gap: 18px;
  }
  .brand__dot {
    width: 60px; height: 60px;
    border: 6px solid var(--orange);
    border-radius: 50%;
  }
  .brand__name {
    color: var(--orange);
    font-weight: 700;
    font-size: 30px;
    letter-spacing: 4px;
    text-transform: uppercase;
  }

  .person {
    position: absolute;
    right: 310px;
    top: 110px;
    color: var(--orange);
    font-family: "Bebas Neue", "Arial Narrow", sans-serif;
    font-weight: 400;
    font-size: 38px;
    line-height: 1;
    letter-spacing: .5px;
    text-align: right;
    white-space: nowrap;
  }
  .divider {
    position: absolute;
    left: 268px;
    top: 104px;
    width: 1px;
    height: 104px;
    background: var(--rule);
  }
  .contacts {
    position: absolute;
    left: 284px;
    top: 104px;
    list-style: none;
  }
  .contacts li {
    display: flex;
    align-items: center;
    gap: 8px;
    height: 21px;
    color: var(--ink);
    font-size: 15px;
    white-space: nowrap;
  }
  .contacts svg { width: 14px; height: 14px; flex: none; fill: var(--orange); }
  .address {
    position: absolute;
    left: 70px;
    top: 232px;
    color: var(--ink);
    font-size: 16px;
    white-space: nowrap;
  }
</style>
</head>
<body>
  <section class="card card--front">
    <div class="brand">
      <span class="brand__dot"></span>
      <span class="brand__name">Coral Pennant</span>
    </div>
  </section>

  <section class="card card--back">
    <h1 class="person">Dale Whitcombe</h1>
    <span class="divider"></span>
    <ul class="contacts">
      <li>
        <svg viewBox="0 0 16 16" aria-hidden="true"><path d="M3.5 1.5l2.5 3-1.5 1.6c.8 1.9 2.3 3.4 4.2 4.2L10.3 8.8l3 2.5-1.2 2.9C6.5 14 2 9.5 1.8 2.7z"/></svg>
        954-731-8842
      </li>
      <li>
        <svg viewBox="0 0 16 16" aria-hidden="true"><path d="M4 1h8v4H4zM1 6h14v6h-3v3H4v-3H1zm4 4v4h6v-4z"/></svg>
        954:731-8843
      </li>
      <li>
        <svg viewBox="0 0 16 16" aria-hidden="true"><path d="M4 1h8v14H4zm1.5 1.5v9h5v-9z"/></svg>
        954-382-1490
      </li>
      <li>
        <svg viewBox="0 0 16 16" aria-hidden="true"><path d="M1 3h14v10H1zm1.5 1.2v.5L8 9l5.5-4.3v-.5z"/></svg>
        dw@coralpennant.com
      </li>
      <li>
        <svg viewBox="0 0 16 16" aria-hidden="true"><path d="M8 1a7 7 0 100 14A7 7 0 008 1zm-1 1.6v2.4H4.4A5.6 5.6 0 017 2.6zm2 0A5.6 5.6 0 0111.6 5H9zM2.5 7H7v2H2.5zm6.5 0h4.5v2H9zm-4.6 4H7v2.4A5.6 5.6 0 014.4 11zM9 11h2.6A5.6 5.6 0 019 13.4z"/></svg>
        www.coralpennant.com
      </li>
    </ul>
    <p class="address">212 North Fenwick Lane Palm Cove, FL 33019</p>
  </section>
</body>
</html>
```